Brookvane Consulting Business Card Design

Business Card Design for Brookvane Consulting. Brookvane Consulting is a boutique consultancy based in Atlanta, GA., that specializes in marketing strategy, organization planning, and leadership development. We provide solutions for small businesses and startups as well as Vantage 300 companies.

http://brookvaneconsulting.com/

Target Market(s)

We provide solutions for small businesses and startups as well as Vantage 300 companies.

Industry/Entity Type

Consulting

Contact Information for Business Card

Two sided business card with priority on contact information, logo, tag line (Inspiration to Dream More, Do More, Become More)

Colors

Designer to choose colors to be used in the design.

Requirements
Must have
• contact information, logo, tag line (Inspiration to Dream More, Do More, Become More)
• Simple no over communication.
Nice to have
• I would like to see different placements of logo and creative use of both sides of the card
Should not have
• Do not put too much information on the card.

```html
<!DOCTYPE html>
<html lang="en">
<head>
<meta charset="utf-8">
<title>Brookvane Consulting – Business Card</title>
<link rel="stylesheet" href="https://fonts.googleapis.com/css2?family=Lato:wght@400;700&family=Open+Sans:wght@400;700&display=swap">
<style>
  :root {
    --page: #ecebe8;
    --card-dark: #2b2b2b;
    --card-light: #ffffff;
    --ink: #222222;
    --ink-soft: #3a3a3a;
    --on-dark: #ffffff;
  }
  * { box-sizing: border-box; margin: 0; padding: 0; }
  html, body { width: 1200px; height: 800px; overflow: hidden; }
  body {
    background: var(--page);
    display: flex;
    align-items: center;
    justify-content: center;
    gap: 60px;
    font-family: "Lato", sans-serif;
  }
  .card {
    width: 525px;
    height: 300px;
    position: relative;
    box-shadow: 0 6px 18px rgba(0,0,0,0.18);
    overflow: hidden;
  }
  .card--front {
    background: var(--card-dark);
    color: var(--on-dark);
    display: flex;
    flex-direction: column;
    align-items: center;
    justify-content: center;
  }
  .brand-name {
    font-family: "Lato", sans-serif;
    font-weight: 700;
    letter-spacing: 1px;
    line-height: 1;
  }
  .card--front .brand-name { font-size: 44px; color: var(--on-dark); }
  .card--front .brand-sub {
    font-family: "Lato", sans-serif;
    font-weight: 700;
    font-size: 26px;
    letter-spacing: 4px;
    text-transform: uppercase;
    margin-top: 10px;
    color: var(--on-dark);
  }
  .card--back {
    background: var(--card-light);
    color: var(--ink);
  }
  .person { position: absolute; left: 42px; top: 40px; }
  .person__name {
    font-family: "Open Sans", sans-serif;
    font-weight: 700;
    font-size: 19px;
    letter-spacing: 0.5px;
  }
  .person__role { font-size: 13px; color: var(--ink-soft); margin-top: -2px; }
  .card--back .brand {
    position: absolute;
    right: 36px;
    top: 78px;
    text-align: right;
    color: var(--ink);
  }
  .card--back .brand-name { font-size: 22px; }
  .card--back .brand-sub {
    font-weight: 700;
    font-size: 12px;
    letter-spacing: 2px;
    text-transform: uppercase;
    margin-top: 4px;
  }
  .contact {
    position: absolute;
    left: 42px;
    top: 118px;
    list-style: none;
    font-size: 13.5px;
    color: var(--ink-soft);
  }
  .contact li { display: flex; align-items: center; gap: 12px; height: 23px; }
  .contact svg { width: 13px; height: 13px; fill: var(--ink); flex: none; }
  .tagline {
    position: absolute;
    left: 42px;
    right: 36px;
    bottom: 44px;
    font-size: 15px;
    color: var(--ink);
  }
  .base-band {
    position: absolute;
    left: 0; right: 0; bottom: 0;
    height: 22px;
    background: var(--card-dark);
  }
</style>
</head>
<body>
  <section class="card card--front" aria-label="Business card front">
    <div class="brand-name">Brookvane</div>
    <div class="brand-sub">Consulting</div>
  </section>

  <section class="card card--back" aria-label="Business card back">
    <div class="person">
      <div class="person__name">JOHN DOE</div>
      <div class="person__role">Manager</div>
    </div>

    <div class="brand">
      <div class="brand-name">Brookvane</div>
      <div class="brand-sub">Consulting</div>
    </div>

    <ul class="contact">
      <li>
        <svg viewBox="0 0 24 24" aria-hidden="true"><path d="M6.6 10.8a15.1 15.1 0 0 0 6.6 6.6l2.2-2.2a1 1 0 0 1 1-.25 11.4 11.4 0 0 0 3.6.57 1 1 0 0 1 1 1V20a1 1 0 0 1-1 1A17 17 0 0 1 3 4a1 1 0 0 1 1-1h3.5a1 1 0 0 1 1 1 11.4 11.4 0 0 0 .57 3.6 1 1 0 0 1-.25 1z"/></svg>
        +12 3555 0142
      </li>
      <li>
        <svg viewBox="0 0 24 24" aria-hidden="true"><path d="M2 5h20v14H2z M2 5l10 8 10-8" fill="none" stroke="#222" stroke-width="2"/><path d="M2 5h20l-10 8z"/></svg>
        email@BrookvaneConsulting.com
      </li>
      <li>
        <svg viewBox="0 0 24 24" aria-hidden="true"><circle cx="12" cy="12" r="10" fill="none" stroke="#222" stroke-width="2"/><ellipse cx="12" cy="12" rx="4" ry="10" fill="none" stroke="#222" stroke-width="2"/><path d="M2 12h20" stroke="#222" stroke-width="2"/></svg>
        www.BrookvaneConsulting.com
      </li>
    </ul>

    <p class="tagline">Inspiration to Dream More, Do More, Become More</p>
    <div class="base-band"></div>
  </section>
</body>
</html>
```